Homemaking training schools needs a Business Card design

Designer, Hello!

No special requirements, good-looking enough.
--------------------------------------------------------------------------

Name: Marcus Dole
Chairman
Tel: 0574-71948263
Mobile: 13857420916
Email: kelvora@mailnest.example
Web: www.prt2019.example
Add: No.258, LanpingJie, BeiyuanQu, Ningbo, Zhejiang

LOGO
Ningbo PRT Homemaking Training School

Target Market(s)

pregnant women, mothers, infants, the elderly and families, including cleaning, cooking, nursing training.

Industry/Entity Type

Business

Contact Information for Business Card

Name: Marcus Dole
Chairman
Tel: 0574-71948263
Mobile: 13857420916
Email: kelvora@mailnest.example
Web: www.prt2019.example

LOGO

Font styles to use
Serif
Sans Serif
Decorative

Requirements
Nice to have
• Feels: clean, specifications, safety, comfort, warmth and happiness.

```html
<!DOCTYPE html>
<html lang="en">
<head>
<meta charset="utf-8">
<title>Pingrui Tang Business Card</title>
<link rel="stylesheet" href="https://fonts.googleapis.com/css2?family=Bebas+Neue&family=Open+Sans:wght@400;600&display=swap">
<style>
  :root {
    --backdrop: #6e4b35;
    --card: #ffffff;
    --accent-blue: #1f6db5;
    --ink: #1c1c1c;
    --ink-soft: #4a4a4a;
    --name-grey: #333333;
    --rule: #2a2a2a;
  }
  * { margin: 0; padding: 0; box-sizing: border-box; }
  html, body { width: 1200px; height: 1000px; overflow: hidden; }
  body {
    position: relative;
    background: var(--backdrop);
    font-family: "Open Sans", Arial, sans-serif;
    color: var(--ink);
  }
  .card {
    position: absolute;
    left: 265px;
    width: 665px;
    height: 397px;
    background: var(--card);
    border-radius: 28px;
    box-shadow: 0 6px 14px rgba(0,0,0,0.35);
  }
  .card--front { top: 73px; }
  .card--back { top: 533px; }

  /* Front */
  .company-name {
    position: absolute;
    top: 200px;
    left: 0; right: 0;
    text-align: center;
    font-family: "Open Sans", Arial, sans-serif;
    font-weight: 600;
    font-size: 44px;
    line-height: 1;
    letter-spacing: 2px;
    color: var(--name-grey);
  }
  .tagline {
    position: absolute;
    top: 258px;
    left: 0; right: 0;
    text-align: center;
    font-size: 20px;
    font-weight: 400;
    color: var(--ink-soft);
  }
  .front-web {
    position: absolute;
    top: 350px;
    left: 0; right: 0;
    text-align: center;
    font-size: 16px;
    color: var(--ink-soft);
  }

  /* Back */
  .person {
    position: absolute;
    right: 350px;
    top: 168px;
    text-align: right;
  }
  .person__name {
    font-family: "Bebas Neue", Arial, sans-serif;
    font-size: 38px;
    line-height: 1;
    color: var(--name-grey);
    letter-spacing: 0.5px;
  }
  .person__title {
    font-size: 16px;
    color: var(--accent-blue);
    margin-top: 2px;
  }
  .divider {
    position: absolute;
    left: 333px;
    top: 152px;
    width: 2px;
    height: 89px;
    background: var(--rule);
  }
  .contacts {
    position: absolute;
    left: 350px;
    top: 152px;
    list-style: none;
  }
  .contacts__item {
    display: flex;
    align-items: center;
    gap: 7px;
    height: 22px;
    font-size: 16px;
    color: var(--ink);
  }
  .contacts__icon { width: 14px; height: 14px; flex: none; }
  .address {
    position: absolute;
    top: 346px;
    left: 0; right: 0;
    text-align: center;
    font-size: 16px;
    color: var(--ink);
  }
</style>
</head>
<body>
  <section class="card card--front">
    <p class="company-name">PINGRUI TANG</p>
    <p class="tagline">Training &amp; Services</p>
    <p class="front-web">www.prt2019.example</p>
  </section>

  <section class="card card--back">
    <div class="person">
      <p class="person__name">MARCUS DOLE</p>
      <p class="person__title">Chairman</p>
    </div>
    <span class="divider"></span>
    <ul class="contacts">
      <li class="contacts__item">
        <svg class="contacts__icon" viewBox="0 0 14 14"><rect x="4" y="1" width="6" height="12" rx="1" fill="none" stroke="#1f6db5" stroke-width="1.4"/><rect x="5.5" y="3" width="3" height="4" fill="#1f6db5"/></svg>
        <span>0574-71948263</span>
      </li>
      <li class="contacts__item">
        <svg class="contacts__icon" viewBox="0 0 14 14"><path d="M1 5 Q7 1 13 5 L11 7 L9 5.5 L5 5.5 L3 7 Z" fill="#1f6db5"/><rect x="3" y="7.5" width="8" height="5" rx="1" fill="#1f6db5"/></svg>
        <span>13857420916</span>
      </li>
      <li class="contacts__item">
        <svg class="contacts__icon" viewBox="0 0 14 14"><rect x="1" y="3" width="12" height="8" fill="#1f6db5"/><path d="M1 3 L7 8 L13 3" fill="none" stroke="#fff" stroke-width="1.2"/></svg>
        <span>kelvora@mailnest.example</span>
      </li>
      <li class="contacts__item">
        <svg class="contacts__icon" viewBox="0 0 14 14"><circle cx="6" cy="6" r="5" fill="none" stroke="#1f6db5" stroke-width="1.6"/><path d="M6 6 L13 9 L10 10 L12 13 L11 13.5 L9 10.5 L7 12.5 Z" fill="#1f6db5"/></svg>
        <span>www.prt2019.example</span>
      </li>
    </ul>
    <p class="address">No.258, LanpingJie, BeiyuanQu, Ningbo, Zhejiang</p>
  </section>
</body>
</html>
```